Business Intelligence Application - Reporting Menu and Report Criteria Design

Looking for a fresh, effective and user friendly view for the menu structure and reporting criteria screen format for a business reporting application. Initial format completed, content structure is in place, but we need the 'wow' design.. as its a serious professional report/BI tool it has to fall within certain guidelines for clarity and graphics..but we want it to be slick, friendly, great user experience. There is a large amount of complex content to fit into a small space and we need it to be very inviting, modern and intuitive.. If interested, please review the attachment. We have live screens in operation, but feel these could be improved and looking forward to seeing what great creative suggestions could be made. Please review work done to date in the attached.. We are not looking for a total re-design of everything, all the basic business content/structure is there.. but tell us what we could do to improve this in terms of graphic design... particularly the criteria screens.. thanks!
Updates

Reason: Need a few more days to review designs - thanks for all submissions so far, we will make a selection shortly.

Target Market(s)

Business analysts, hotel operations teams, finance analysts hospitality industry

Industry/Entity Type

Hospitality

Coding

Coded - Design and coding required

Number of Pages Required

4 page

Font styles to use
Sans Serif
Other font styles liked:
• Candara, please see example in deck

Colors
3276b5
3176b5
0255a3
85acd3
33a6d7
cee9f5
85cae6

Requirements
Must have
• sharp clear, logical menu structure, (currently it has 'clicks to sub-menus, we need hover over, slide to sub-menus..) colour, styling.. and most focus on revision of criteria.. right now is somewhat heavy, cumbersome.. keep colour and friendly intuitive process steps.. its heavy analytical stuff.. best of luck!
Should not have
• No grey fonts on white or grey screens! many business apps are not readable or sharp.. or fonts are too small.. colourless, so please avoid that.. see our deck - sharp dark (navy) or black fonts on white, or light shading..

```html
<!DOCTYPE html>
<html lang="en">
<head>
<meta charset="utf-8">
<title>Amber Coast Hotels &amp; Suites – Rollup Criteria</title>
<link href="https://fonts.googleapis.com/css2?family=Cabin:wght@400;500;600&display=swap" rel="stylesheet">
<style>
:root{
  --header-bg:#d3eaf6;
  --brand:#33a6d7;
  --panel:#35a7d8;
  --ink:#10202e;
  --white:#ffffff;
  --field-line:#9aa4ab;
}
*{box-sizing:border-box;margin:0;padding:0}
html,body{width:1200px;height:938px;overflow:hidden;background:var(--white);font-family:"Cabin",sans-serif;color:var(--ink)}
.app{position:relative;width:1200px;height:938px}
.topbar{position:absolute;left:0;top:0;width:1200px;height:60px;background:var(--header-bg)}
.brand{position:absolute;left:48px;top:15px;display:flex;align-items:center;gap:9px;color:var(--brand);font-size:19px;font-weight:500}
.brand-dot{width:30px;height:30px;border-radius:50%;background:var(--brand)}
.welcome{position:absolute;top:22px;font-size:13px;font-weight:600}
.top-btn{position:absolute;top:11px;height:37px;background:var(--brand);color:var(--white);font-size:13px;font-weight:600;display:flex;align-items:center;justify-content:center;letter-spacing:.3px}
.top-icon{position:absolute;top:16px}
.mainnav{position:absolute;left:48px;top:90px;display:flex;align-items:center;font-size:13.5px;font-weight:500}
.mainnav span.sep{color:var(--brand);margin:0 9px;font-size:10px}
.mainnav .link{color:var(--brand)}
.search{position:absolute;left:775px;top:81px;width:374px;height:37px;border:1px solid var(--field-line);font-size:11.5px;display:flex;align-items:center;padding-left:17px;letter-spacing:.2px}
.search svg{position:absolute;right:10px;top:11px}
.subnav{position:absolute;left:333px;top:123px;width:430px;height:37px;background:var(--brand);color:var(--white);font-size:13px;font-weight:600;display:flex;align-items:center;padding-left:14px}
.subnav .sep{margin:0 8px;font-size:9px}
.caret{position:absolute;width:0;height:0;border-left:12px solid transparent;border-right:12px solid transparent;border-bottom:12px solid var(--brand)}
.panel{position:absolute;left:331px;top:189px;width:583px;height:701px;background:var(--panel)}
.section-title{position:absolute;color:var(--white);font-size:21px;font-weight:600}
.field{position:absolute;height:40px;background:var(--white);font-size:11px;display:flex;align-items:center;padding-left:13px}
.field .arrow{position:absolute;right:12px;top:17px;width:0;height:0;border-left:4.5px solid transparent;border-right:4.5px solid transparent;border-top:5px solid #555}
.field svg{position:absolute;right:10px;top:13px}
.l{left:25px;width:260px}.r{left:298px;width:259px}
.h1{left:298px;width:125px}.h2{left:431px;width:125px}
</style>
</head>
<body>
<div class="app">
  <header class="topbar">
    <div class="brand"><span class="brand-dot"></span>Amber Coast Hotels &amp; Suites</div>
    <div class="welcome" style="left:556px">Welcome Admin</div>
    <div class="welcome" style="left:668px">Tuesday October 04.2017</div>
    <div class="top-btn" style="left:834px;width:107px">INTEL</div>
    <div class="top-btn" style="left:957px;width:107px">PLANNING</div>
    <svg class="top-icon" style="left:1083px" width="28" height="26" viewBox="0 0 28 26" fill="none" stroke="#222" stroke-width="1.3"><path d="M8 18c2-2 1-6 2-9a4 4 0 0 1 8 0c1 3 0 7 2 9z"/><path d="M12 20a2 2 0 0 0 4 0"/><path d="M5 9c-1 2-1 4 0 6M23 9c1 2 1 4 0 6"/></svg>
    <svg class="top-icon" style="left:1125px" width="30" height="24" viewBox="0 0 30 24" fill="none" stroke="#222" stroke-width="1.3"><path d="M3 8v13h20v-5"/><path d="M9 17c1-6 6-9 13-9V4l6 6-6 6v-4c-5 0-10 1-13 5z"/></svg>
  </header>

  <nav class="mainnav">
    <span>Admin</span><span class="sep">•</span>
    <span class="link">Management</span><span class="sep">•</span>
    <span class="link">Rooms Performance</span><span class="sep">•</span>
    <span class="link">Revenue Summary</span><span class="sep">•</span>
    <span>Demand &amp; Risk</span><span class="sep">•</span>
    <span>Inventory Analysis</span><span class="sep">•</span>
    <span>Placeholder</span>
  </nav>
  <div class="search">PROPERTY SEARCH
    <svg width="14" height="14" viewBox="0 0 14 14" fill="none" stroke="#222" stroke-width="1.3"><circle cx="6" cy="6" r="4.8"/><path d="M9.5 9.5 13 13"/></svg>
  </div>

  <div class="caret" style="left:346px;top:111px"></div>
  <div class="subnav">
    <span>Rollup Criteria</span><span class="sep">•</span>
    <span>Report Criteria</span><span class="sep">•</span>
    <span>Edit View</span><span class="sep">•</span>
    <span>Saved View</span><span class="sep">•</span>
    <span>Export</span>
  </div>

  <div class="caret" style="left:366px;top:174px;border-left-width:15px;border-right-width:15px;border-bottom-width:15px"></div>
  <section class="panel">
    <h2 class="section-title" style="left:24px;top:18px">Geographic / Management Regions</h2>
    <div class="field l" style="top:63px">Select Division<span class="arrow"></span></div>
    <div class="field r" style="top:63px">Select Group<span class="arrow"></span></div>
    <div class="field l" style="top:115px">Select Region<span class="arrow"></span></div>
    <div class="field r" style="top:115px">Select Property<span class="arrow"></span></div>
    <div class="field l" style="top:167px">Select Area<span class="arrow"></span></div>
    <div class="field r" style="top:167px">Select Property ID<span class="arrow"></span></div>
    <div class="field l" style="top:219px">Select City<span class="arrow"></span></div>
    <div class="field r" style="top:219px">Select Country<span class="arrow"></span></div>

    <h2 class="section-title" style="left:25px;top:281px">Operational / BI Filters</h2>
    <div class="field l" style="top:322px">Brands<span class="arrow"></span></div>
    <div class="field h1" style="top:322px">Opening Date
      <svg width="13" height="13" viewBox="0 0 13 13" fill="none" stroke="#777"><rect x=".5" y="1.5" width="12" height="11"/><path d="M.5 4.5h12M3.5 0v3M9.5 0v3M3 7h1M6 7h1M9 7h1M3 10h1M6 10h1M9 10h1"/></svg></div>
    <div class="field h2" style="top:322px">
      <svg width="13" height="13" viewBox="0 0 13 13" fill="none" stroke="#777"><rect x=".5" y="1.5" width="12" height="11"/><path d="M.5 4.5h12M3.5 0v3M9.5 0v3M3 7h1M6 7h1M9 7h1M3 10h1M6 10h1M9 10h1"/></svg></div>
    <div class="field l" style="top:374px">Rating<span class="arrow"></span></div>
    <div class="field h1" style="top:374px">From</div>
    <div class="field h2" style="top:374px">To<span class="arrow"></span></div>
    <div class="field l" style="top:426px">Hotel Type<span class="arrow"></span></div>
    <div class="field r" style="top:426px">PMS System<span class="arrow"></span></div>
    <div class="field l" style="top:478px">F&amp;B Service<span class="arrow"></span></div>
    <div class="field r" style="top:478px">Finance System<span class="arrow"></span></div>

    <h2 class="section-title" style="left:28px;top:541px">Currency Conversion</h2>
    <div class="field l" style="top:583px">Rollup Currency<span class="arrow"></span></div>
    <div class="field r" style="top:583px">YOY Analysis<span class="arrow"></span></div>
    <div class="field l" style="top:635px">Conversion Rate<span class="arrow"></span></div>
    <div class="field r" style="top:635px">Same Store<span class="arrow"></span></div>
  </section>
</div>
</body>
</html>
```